American cannabis tech company business card design

Pavrel.com is seeking a modern, professional, and brand-aligned business card that represents our company and its core values: Mission, Story, Values, and Impact. As an innovative cannabis company, we want a business card that is not only visually appealing but also serves as a representation of who we are and what we stand for.

Project Scope: Design a double-sided business card that integrates our brand identity and core values. Incorporate our key brand elements, ensuring a sleek and contemporary aesthetic. Visually reflect our core values (Mission, Story, Values, Impact) in a way that is engaging yet professional.

Target Market(s)

Vendors, third parties,

Contact Information for Business Card

Contact details (name, title, email, phone, website, etc.)

Font styles to use
Other font styles liked:
• Caslon, Centra

Colors

Designer to choose colors to be used in the design.

Requirements
Must have
• Pavrel.com logo and branding A creative yet clean way to integrate our core values (Mission, Story, Values, Impact) Modern typography and a well-structured layout
Nice to have
• forest green, grey, white, black
Should not have
• references to marijuana, leafs, plants, or related product

```html
<!DOCTYPE html>
<html lang="en">
<head>
<meta charset="utf-8">
<title>Pavrel.com Business Card</title>
<link rel="stylesheet" href="https://fonts.googleapis.com/css2?family=Libre+Caslon+Text:wght@400;700&family=Montserrat:wght@400;500&display=swap">
<style>
  :root {
    --stage: #1e1f1e;
    --forest-deep: #0f2612;
    --forest: #1c4020;
    --forest-mid: #2a4a2b;
    --forest-band: #29412a;
    --forest-light: #2f6b34;
    --paper: #ffffff;
    --ink: #1a1a1a;
    --ink-green: #1d3a20;
  }
  * { box-sizing: border-box; margin: 0; padding: 0; }
  html, body {
    width: 1200px; height: 900px; overflow: hidden;
    background: var(--stage);
  }
  .stage { position: relative; width: 1200px; height: 900px; }
  .card {
    position: absolute;
    width: 620px; height: 354px;
    border-radius: 22px;
    overflow: hidden;
    box-shadow: 0 18px 40px rgba(0,0,0,0.55);
  }
  /* Front */
  .card-front {
    left: 110px; top: 96px;
    background: linear-gradient(160deg, var(--forest) 0%, var(--forest-deep) 60%, #0c1f0f 100%);
  }
  .front-pattern {
    position: absolute; inset: 0;
    background: linear-gradient(115deg, rgba(47,107,52,0.75) 0%, rgba(30,70,34,0.35) 35%, rgba(15,38,18,0) 70%);
  }
  .front-brand {
    position: absolute; right: 120px; top: 170px;
    font-family: "Libre Caslon Text", Georgia, serif;
    font-weight: 700; font-size: 30px; letter-spacing: 0.5px;
    color: var(--paper);
  }
  /* Back */
  .card-back {
    left: 470px; top: 452px;
    background: var(--paper);
  }
  .back-band {
    position: absolute; top: 0; right: 0; bottom: 0; width: 190px;
    background: var(--forest-band);
    display: flex; align-items: center; justify-content: center;
  }
  .band-brand {
    font-family: "Libre Caslon Text", Georgia, serif;
    font-weight: 700; font-size: 66px;
    color: var(--forest-light);
    transform: rotate(90deg);
    white-space: nowrap;
  }
  .person {
    position: absolute; left: 46px; top: 44px;
    font-family: "Libre Caslon Text", Georgia, serif;
    color: var(--ink-green);
  }
  .person-name { font-size: 22px; font-weight: 700; }
  .person-title { font-size: 11px; font-weight: 700; color: var(--ink); margin-top: 2px; margin-left: 16px; }
  .contact {
    position: absolute; left: 82px; bottom: 40px;
    font-family: "Montserrat", Arial, sans-serif;
    font-size: 13px; color: var(--ink); line-height: 1.3;
  }
  .address { margin-bottom: 16px; margin-left: 4px; }
  .contact-row { display: flex; align-items: center; gap: 8px; margin-bottom: 5px; }
  .contact-row svg { width: 13px; height: 13px; fill: var(--ink-green); flex: none; }
</style>
</head>
<body>
<main class="stage">
  <section class="card card-front">
    <div class="front-pattern" role="img" aria-label="Repeating brand wordmark pattern fading from bright to deep forest green"></div>
    <div class="front-brand">PAVREL</div>
  </section>

  <section class="card card-back">
    <div class="person">
      <div class="person-name">Dana Keller</div>
      <div class="person-title">Owner</div>
    </div>
    <div class="contact">
      <div class="address">418 Harbor Lane, #112<br>Riverton, OH 43210</div>
      <div class="contact-row">
        <svg viewBox="0 0 24 24" aria-hidden="true"><path d="M6.6 10.8a15.1 15.1 0 0 0 6.6 6.6l2.2-2.2a1 1 0 0 1 1-.25 11.4 11.4 0 0 0 3.6.6 1 1 0 0 1 1 1V20a1 1 0 0 1-1 1A17 17 0 0 1 3 4a1 1 0 0 1 1-1h3.5a1 1 0 0 1 1 1c0 1.25.2 2.45.6 3.6a1 1 0 0 1-.25 1z"/></svg>
        <span>555-210-0148</span>
      </div>
      <div class="contact-row">
        <svg viewBox="0 0 24 24" aria-hidden="true"><path d="M2 5h20v14H2z M2 5l10 8 10-8" fill="none" stroke="#1d3a20" stroke-width="2"/><path d="M2 5h20l-10 8z"/></svg>
        <span>info@pavrel.com</span>
      </div>
      <div class="contact-row">
        <svg viewBox="0 0 24 24" aria-hidden="true"><circle cx="12" cy="12" r="10"/><path d="M2 12h20M12 2c3 3 3 17 0 20M12 2c-3 3-3 17 0 20" fill="none" stroke="#fff" stroke-width="1.4"/></svg>
        <span>www.pavrel.com</span>
      </div>
    </div>
    <div class="back-band">
      <div class="band-brand">PAVREL</div>
    </div>
  </section>
</main>
</body>
</html>
```